Photojournalism/photography business needs a simple, timeless & professional letterhead design

We need a letterhead design for photography/photojournalism business called 'plunq', no capitals.

The letterhead needs to be:
- simple
- professional
- timeless
- easy to read
- consists of at least 2 colors to make it stands out.

We do mainly editorial photography, photo articles for various publications, travel, businesses, as well as people such as family and kids.

The final design should communicate professionalism, easy identification, attention grabbing, even if it has to be found among a stack of various papers on the clients' desks.

Target Market(s)

Various publications.

Industry/Entity Type

Business

Requirements
Must have
• Please use the logo attached.

```html
<!DOCTYPE html>
<html lang="en">
<head>
<meta charset="utf-8">
<title>plunq stationery</title>
<link href="https://fonts.googleapis.com/css2?family=Tinos:wght@400;700&display=swap" rel="stylesheet">
<style>
  :root {
    --plum: #7b4761;
    --plum-dark: #6e3d56;
    --paper: #ffffff;
    --paper-shade: #ececec;
    --ink: #1c1c1c;
    --body-ink: #3a3a3a;
    --rule: #9a9a9a;
    --stage: #000000;
  }
  * { box-sizing: border-box; margin: 0; padding: 0; }
  html, body { width: 1200px; height: 848px; overflow: hidden; background: var(--stage); }
  body { font-family: "Tinos", "Times New Roman", serif; position: relative; }

  .brand-name { font-family: "Tinos", "Times New Roman", serif; font-weight: 700; letter-spacing: -0.02em; line-height: 1; }
  .brand-square { display: inline-block; border: 2px solid currentColor; }

  /* folder */
  .folder { position: absolute; left: 118px; top: 137px; width: 440px; height: 623px; background: var(--plum); }
  .folder .brand-name { position: absolute; left: 150px; top: 262px; font-size: 66px; color: var(--paper); }

  /* letterhead */
  .letterhead { position: absolute; left: 421px; top: 65px; width: 442px; height: 624px; background: var(--plum); }
  .letterhead .sheet { position: absolute; inset: 0; border-bottom-right-radius: 96px;
    background: linear-gradient(180deg, #fafafa 0%, var(--paper-shade) 45%, #f6f6f6 70%, var(--paper-shade) 100%); }
  .letterhead .corner { position: absolute; left: 0; top: 0; }
  .lh-header { position: absolute; left: 88px; top: 2px; height: 68px; display: flex; align-items: center; }
  .lh-header .brand-name { font-size: 38px; color: var(--ink); width: 117px; }
  .rule-v { width: 1px; align-self: stretch; background: var(--rule); }
  .contact { font-size: 5.4px; line-height: 7px; color: var(--ink); padding: 0 18px; width: 131px; }
  .lh-header .brand-square { color: var(--ink); width: 38px; height: 38px; margin-left: 20px; }
  .lh-body { position: absolute; left: 88px; top: 146px; width: 265px; font-size: 7.6px; line-height: 13.35px;
    color: var(--body-ink); text-align: justify; }
  .lh-body p { margin-bottom: 13.5px; }

  /* envelope with banner */
  .envelope-banner { position: absolute; left: 630px; top: 154px; width: 490px; height: 219px; background: var(--paper);
    box-shadow: 0 2px 4px rgba(0,0,0,.25); }
  .envelope-banner .band { position: absolute; left: 0; top: 0; width: 490px; height: 68px; }
  .eb-header { position: absolute; left: 109px; top: 0; height: 68px; display: flex; align-items: center; }
  .eb-header .brand-name { font-size: 36px; color: var(--paper); width: 100px; }
  .eb-header .rule-v { background: rgba(255,255,255,.7); }
  .eb-header .contact { color: var(--paper); font-weight: 700; font-size: 4.6px; line-height: 6px; padding: 0 16px; width: 113px; }
  .eb-header .brand-square { color: var(--paper); width: 34px; height: 34px; margin-left: 18px; }

  /* window envelope */
  .envelope-window { position: absolute; left: 628px; top: 404px; width: 491px; height: 218px; background: var(--plum); }
  .envelope-window .sheet { position: absolute; inset: 0; background: var(--paper); border-bottom-right-radius: 102px; }
  .envelope-window .corner { position: absolute; left: 0; top: 0; }
  .ew-mark { position: absolute; left: 90px; top: 10px; display: flex; flex-direction: column; align-items: center; color: var(--plum); }
  .ew-mark .brand-name { font-size: 20px; }
  .ew-mark .brand-square { width: 34px; height: 34px; margin-top: 8px; }
  .address-window { position: absolute; left: 43px; top: 109px; width: 144px; height: 57px; background: #f3f3f3;
    box-shadow: inset 0 0 3px rgba(0,0,0,.25), 0 2px 3px rgba(0,0,0,.15); }
</style>
</head>
<body>

<section class="folder">
  <span class="brand-name">plunq</span>
</section>

<section class="letterhead">
  <div class="sheet"></div>
  <svg class="corner" width="70" height="70" viewBox="0 0 70 70"><polygon points="0,0 68,0 0,68" fill="var(--plum)"/></svg>
  <header class="lh-header">
    <span class="brand-name">plunq</span>
    <span class="rule-v"></span>
    <div class="contact">Lorem ipsum dolor sit amet,<br>consectetur adipisicing elit, sed do<br>eiusmod tempor incididunt ut labore<br>www.plunq.com.au<br>0400 555 120</div>
    <span class="rule-v"></span>
    <span class="brand-square"></span>
  </header>
  <div class="lh-body">
    <p>Lorem ipsum dolor sit amet, consectetur adipisicing elit, sed do eiusmod tempor incididunt ut labore et dolore magna aliqua. Ut enim ad minim veniam, quis nostrud exercitation ullamco laboris nisi ut aliquip ex ea commodo consequat. Duis aute irure dolor in reprehenderit in voluptate velit esse cillum dolore eu fugiat nulla pariatur. Excepteur sint occaecat cupidatat non proident, sunt in culpa qui officia deserunt mollit anim id est laborum.</p>
    <p>Lorem ipsum dolor sit amet, consectetur adipisicing elit, sed do eiusmod tempor incididunt ut labore et dolore magna aliqua. Ut enim ad minim veniam, quis nostrud exercitation ullamco laboris nisi ut aliquip ex ea commodo consequat. Duis aute irure dolor in reprehenderit in voluptate velit esse cillum dolore eu fugiat nulla pariatur. Excepteur sint occaecat cupidatat non proident, sunt in culpa qui officia deserunt mollit anim id est laborum.</p>
    <p>Lorem ipsum dolor sit amet, consectetur adipisicing elit, sed do eiusmod tempor incididunt ut labore et dolore magna aliqua. Ut enim ad minim veniam, quis nostrud exercitation ullamco laboris nisi ut aliquip ex ea commodo consequat. Duis aute irure dolor in reprehenderit in voluptate velit esse cillum dolore eu fugiat nulla pariatur. Excepteur sint occaecat cupidatat non proident, sunt in culpa qui officia deserunt mollit anim id est laborum.</p>
    <p>Lorem ipsum dolor sit amet, consectetur adipisicing elit, sed do eiusmod tempor incididunt ut labore et dolore magna aliqua. Ut enim ad minim veniam, quis nostrud exercitation ullamco laboris nisi ut aliquip ex ea commodo consequat. Duis aute irure dolor in reprehenderit in voluptate velit esse cillum dolore eu fugiat nulla pariatur. Excepteur sint occaecat cupidatat non proident, sunt in culpa qui officia deserunt mollit anim id est laborum.</p>
  </div>
</section>

<section class="envelope-banner">
  <svg class="band" viewBox="0 0 490 68" preserveAspectRatio="none"><polygon points="0,0 490,0 486,68 4,68" fill="var(--plum)"/></svg>
  <header class="eb-header">
    <span class="brand-name">plunq</span>
    <span class="rule-v"></span>
    <div class="contact">Lorem ipsum dolor sit amet,<br>consectetur adipisicing elit, sed do<br>eiusmod tempor incididunt ut labore<br>www.plunq.com.au<br>0400 555 120</div>
    <span class="rule-v"></span>
    <span class="brand-square"></span>
  </header>
</section>

<section class="envelope-window">
  <div class="sheet"></div>
  <svg class="corner" width="82" height="82" viewBox="0 0 82 82"><polygon points="0,0 0,82 81,0" fill="var(--plum)" transform="matrix(1 0 0 1 0 0)"/></svg>
  <div class="ew-mark">
    <span class="brand-name">plunq</span>
    <span class="brand-square"></span>
  </div>
  <div class="address-window"></div>
</section>

</body>
</html>
```